Paul Denton Sausage Label Design

Halvern Fields Corporation is seeking to create a new brand of fresh 100% Canadian pork sausage. This label will be a paper band that slips on and off foam trays. The front facing side will be 5 inches wide by 3.5 inches high. The following is some information about our brand.
Target market:
1. Working Moms
2. Stay at home moms
3. Barbeque enthusiast
Brand personality
1. Old school values – We are a family run company who believes in an honest days work
2. Modern day sensibility – We believe in being nimble and open to new ideas
3. Energetic and optimistic – We are passionate about our business and product
4. Relaxed sense of humor – We believe that it is possible to work hard and have fun
Positioning Statements:
Our sausage is the easy choice for adding flavour to your real- life family meals, that’s because:
1. It is 100% fresh Canadian product with no fillers or preservatives
2. It is a great tasting recipe with simple, natural ingredients
3. It is brought to you with good humor and integrity by a multi- generational family owned business
We are looking for a creative designer to make our ideas come to life. There are three types of designs we would like to see:
1. Rustic – a rustic, barbequing, old farm, country feel – without feeling too old
2. Modern & Simple – Very simple clean face with clean text
3. Family friendly – a label that would appeal to the everyday family with photos of the finished product
This brand does not have a name yet, please use the name “Paul Denton “as a place holder. Please keep in mind the information provided about our brand when developing the label. Attached are pictures of some ideas we like. Please do not copy these ideas too closely, we are looking to differentiate ourselves in the market. Samples are to provide some guidance of our preferences.
Target Market(s)
1. Working Moms
2. Stay at home moms
3. Barbeque enthusiast
Colors
Designer to choose colors to be used in the design.

```html
<!DOCTYPE html>
<html lang="en">
<head>
<meta charset="utf-8">
<title>Paul Denton – Mutton &amp; Mint Sausage Label</title>
<link href="https://fonts.googleapis.com/css2?family=Alfa+Slab+One&family=Arvo:wght@400;700&family=Yellowtail&display=block" rel="stylesheet">
<style>
  :root {
    --label-orange: #da862d;
    --cream: #eeeedd;
    --brown: #5a3612;
    --illustration-light: #f3efe6;
    --illustration-red: #b8553a;
  }
  html, body {
    margin: 0;
    padding: 0;
    width: 1200px;
    height: 843px;
    overflow: hidden;
    background: var(--label-orange);
  }
  .label {
    position: relative;
    width: 1200px;
    height: 843px;
    background: var(--label-orange);
    color: var(--cream);
    font-family: "Arvo", "Rockwell", serif;
    font-weight: 700;
  }
  .label p, .label h1, .label h2 { margin: 0; white-space: nowrap; }
  .rule { position: absolute; background: var(--cream); }
  .rule--h { height: 4px; }
  .rule--v { width: 4px; }

  .corporation {
    position: absolute;
    left: 46px;
    top: 66px;
    font-size: 24px;
    line-height: 32px;
    letter-spacing: 0.5px;
  }
  .brand-name {
    position: absolute;
    left: 34px;
    top: 166px;
    font-family: "Alfa Slab One", "Rockwell Extra Bold", serif;
    font-weight: 400;
    font-size: 88px;
    line-height: 124px;
    color: var(--cream);
    text-shadow: 6px 5px 0 var(--brown);
  }
  .brand-name span { display: block; }

  .mascot-art {
    position: absolute;
    left: 530px;
    top: 14px;
    width: 600px;
    height: 438px;
  }

  .map-art {
    position: absolute;
    left: 60px;
    top: 500px;
    width: 178px;
    height: 172px;
  }
  .origin {
    position: absolute;
    left: 250px;
    top: 476px;
    font-family: "Yellowtail", cursive;
    font-weight: 400;
    font-size: 32px;
    line-height: 30px;
  }
  .claim {
    position: absolute;
    left: 428px;
    top: 466px;
    font-family: "Yellowtail", cursive;
    font-weight: 400;
    font-size: 46px;
    line-height: 64px;
  }
  .flavour {
    position: absolute;
    left: 428px;
    top: 556px;
    font-family: "Alfa Slab One", "Rockwell Extra Bold", serif;
    font-weight: 400;
    font-size: 54px;
    line-height: 64px;
    color: var(--brown);
    letter-spacing: 0.5px;
  }
  .product-type {
    position: absolute;
    left: 438px;
    top: 626px;
    font-size: 33px;
    line-height: 40px;
  }
  .count {
    position: absolute;
    left: 68px;
    top: 722px;
    font-size: 29px;
    line-height: 36px;
  }
  .weight {
    position: absolute;
    left: 190px;
    top: 712px;
    font-size: 33px;
    line-height: 44px;
  }
  .weight .estimated {
    font-family: "Arvo", serif;
    font-weight: 400;
    font-size: 44px;
    margin-left: 8px;
  }
  .storage {
    position: absolute;
    left: 191px;
    top: 757px;
    font-size: 17.5px;
    line-height: 22px;
  }
  .description {
    position: absolute;
    left: 438px;
    top: 708px;
    font-size: 33px;
    line-height: 41px;
    letter-spacing: 0.3px;
  }
</style>
</head>
<body>
<main class="label">
  <div class="rule rule--h" style="left:42px; top:121px; width:466px;"></div>
  <div class="rule rule--v" style="left:506px; top:44px; height:414px;"></div>
  <div class="rule rule--h" style="left:38px; top:457px; width:1123px;"></div>
  <div class="rule rule--v" style="left:406px; top:459px; height:341px;"></div>
  <div class="rule rule--h" style="left:408px; top:542px; width:753px;"></div>
  <div class="rule rule--h" style="left:38px; top:690px; width:1123px;"></div>
  <div class="rule rule--v" style="left:156px; top:692px; height:108px;"></div>

  <p class="corporation">HALVERN FIELDS CORPORATION</p>
  <h1 class="brand-name"><span>PAUL</span><span>DENTON</span></h1>

  <svg class="mascot-art" role="img" aria-label="Illustration: cheerful chef mascot holding a grilled sausage on a fork" viewBox="0 0 600 438">
    <defs>
      <linearGradient id="mascotTone" x1="0" y1="0" x2="1" y2="0">
        <stop offset="0" stop-color="var(--illustration-red)" stop-opacity="0.55"/>
        <stop offset="1" stop-color="var(--illustration-light)" stop-opacity="0.6"/>
      </linearGradient>
    </defs>
    <rect x="0" y="0" width="600" height="438" rx="24" fill="url(#mascotTone)"/>
  </svg>

  <svg class="map-art" role="img" aria-label="Map of Canada" viewBox="0 0 178 172">
    <rect x="0" y="0" width="178" height="172" rx="12" fill="var(--cream)"/>
  </svg>
  <p class="origin">100%<br>Canadian</p>

  <p class="claim">All Natural</p>
  <h2 class="flavour">MUTTON &amp; MINT</h2>
  <p class="product-type">PORK SAUSAGES</p>

  <p class="count">X6</p>
  <p class="weight">400G<span class="estimated">&#8494;</span></p>
  <p class="storage">KEEP REFRIGERATED</p>

  <p class="description">6 MATURE MUTTON&nbsp; SAUSAGE,<br>INFUSED WITH MINT.</p>
</main>
</body>
</html>
```